RWT Fittings Ltd Business Cards

We need a business card with our business logo. We provide window and door installations on high-rises in west coast British Colombia, Canada.

I would like my business information and details on one side of the card, and the other side the company name with logo

Target Market(s)

General Contractors

Industry/Entity Type

Construction

Contact Information for Business Card

one side i want my company name and logo in the dark theme logo that i provided

Requirements
Must have
• Marco Peltieri, 16045518293, RWTFittings@mailbox-demo.com, 1407-5194 Linden Row Burnaby BC, V5H 2K9, Owner & Manager

```html
<!DOCTYPE html>
<html lang="en">
<head>
<meta charset="utf-8">
<title>RWT Fittings Ltd Business Cards</title>
<link href="https://fonts.googleapis.com/css2?family=Poppins:wght@300;400;700&display=swap" rel="stylesheet">
<style>
  :root {
    --page-bg: #d8d8d8;
    --card-bg: #2b2b2b;
    --brand-blue: #1fa3dd;
    --text-light: #f2f2f2;
    --rule-blue: #1f9ad2;
  }
  * { margin: 0; padding: 0; box-sizing: border-box; }
  html, body {
    width: 1200px; height: 965px; overflow: hidden;
    background: var(--page-bg);
    font-family: 'Poppins', sans-serif;
  }
  .canvas { position: relative; width: 1200px; height: 965px; }
  .card {
    position: absolute; top: 159px;
    width: 383px; height: 668px;
    background: var(--card-bg);
  }
  .card--front { left: 186px; }
  .card--back { left: 653px; overflow: hidden; }

  .brand {
    position: absolute; top: 84px; left: 0; right: 0;
    display: flex; align-items: center; justify-content: center; gap: 12px;
  }
  .brand__square { width: 34px; height: 34px; background: var(--brand-blue); }
  .brand__name {
    color: var(--brand-blue); font-weight: 700; font-size: 31px;
    line-height: 1.1; letter-spacing: 0.5px;
  }

  .person { position: absolute; top: 396px; left: 0; right: 0; text-align: center; }
  .person__name {
    color: var(--brand-blue); font-weight: 700; font-size: 25px; line-height: 1.2;
  }
  .person__title { color: var(--text-light); font-weight: 300; font-size: 15px; line-height: 1.3; }

  .contact-icons {
    position: absolute; top: 461px; left: 27px; right: 27px;
    display: flex; align-items: center; justify-content: center; gap: 7px;
  }
  .contact-icons__rule { flex: 1; height: 1.5px; background: var(--rule-blue); }
  .contact-icons__rule--left { margin-right: 5px; }
  .contact-icons__rule--right { margin-left: 5px; }
  .contact-icons svg { display: block; }

  .contact { position: absolute; top: 494px; left: 0; right: 0; text-align: center; }
  .contact__line {
    color: var(--text-light); font-weight: 300; font-size: 16px; line-height: 20px;
  }

  .divider {
    position: absolute; top: 570px; left: 30px; right: 30px;
    height: 1.5px; background: var(--rule-blue);
  }
  .address {
    position: absolute; top: 580px; left: 0; right: 0; text-align: center;
    color: var(--text-light); font-weight: 300; font-size: 16px;
  }

  .back-pattern {
    position: absolute; inset: 0;
    background: linear-gradient(160deg, #8a8a8a 0%, #555 35%, #262626 65%, #111 100%);
  }
  .back-brand {
    position: absolute; top: 314px; left: 0; right: 0;
    display: flex; align-items: center; justify-content: center; gap: 8px;
  }
  .back-brand__square { width: 18px; height: 18px; background: var(--brand-blue); }
  .back-brand__name { color: var(--brand-blue); font-weight: 700; font-size: 17px; }
</style>
</head>
<body>
<main class="canvas">
  <section class="card card--front">
    <div class="brand">
      <span class="brand__square"></span>
      <span class="brand__name">RWT Fittings Ltd</span>
    </div>

    <div class="person">
      <p class="person__name">MARCO PELTIERI</p>
      <p class="person__title">Owner &amp; Manager</p>
    </div>

    <div class="contact-icons">
      <span class="contact-icons__rule contact-icons__rule--left"></span>
      <svg width="22" height="22" viewBox="0 0 22 22" aria-label="Phone">
        <circle cx="11" cy="11" r="11" fill="var(--brand-blue)"/>
        <path d="M8 5.5l2 2.6-1.2 1.3c.6 1.5 1.6 2.6 3 3.3l1.3-1.2 2.5 2-1 1.8c-3.8.2-7.5-3.8-7.5-8z" fill="#fff"/>
      </svg>
      <svg width="22" height="22" viewBox="0 0 22 22" aria-label="Email">
        <circle cx="11" cy="11" r="11" fill="var(--brand-blue)"/>
        <rect x="5.5" y="7.5" width="11" height="7.5" rx="1" fill="none" stroke="#fff" stroke-width="1.3"/>
        <path d="M5.8 8l5.2 4 5.2-4" fill="none" stroke="#fff" stroke-width="1.3"/>
      </svg>
      <svg width="22" height="22" viewBox="0 0 22 22" aria-label="Website">
        <circle cx="11" cy="11" r="11" fill="var(--brand-blue)"/>
        <g fill="none" stroke="#fff" stroke-width="1.1">
          <circle cx="11" cy="11" r="6"/>
          <ellipse cx="11" cy="11" rx="2.6" ry="6"/>
          <path d="M5 11h12M6 8h10M6 14h10"/>
        </g>
      </svg>
      <span class="contact-icons__rule contact-icons__rule--right"></span>
    </div>

    <div class="contact">
      <p class="contact__line">16045518293</p>
      <p class="contact__line">RWTFittings@mailbox-demo.com</p>
      <p class="contact__line">www.rwtfittings-demo.com</p>
    </div>

    <div class="divider"></div>
    <p class="address">1407-5194 Linden Row Burnaby BC, V5H 2K9</p>
  </section>

  <section class="card card--back">
    <div class="back-pattern" role="img" aria-label="Repeating company mark pattern fading from light grey at top to black at bottom"></div>
    <div class="back-brand">
      <span class="back-brand__square"></span>
      <span class="back-brand__name">RWT Fittings Ltd</span>
    </div>
  </section>
</main>
</body>
</html>
```